Software allocation system needs a business card design

We need a business card designed for our software platform - www.tallivo.com.au

At the moment the logo and website is all black and white, we are happy for suggestions on implementing some colour throughout either the logo or business card.

Industry/Entity Type

Software

Font styles to use
Sans Serif

Colors

Designer to choose colors to be used in the design.

```html
<!DOCTYPE html>
<html lang="en">
<head>
<meta charset="utf-8">
<title>Tallivo Business Card</title>
<link rel="stylesheet" href="https://fonts.googleapis.com/css2?family=Cabin+Condensed:wght@400;500&family=Josefin+Sans:wght@400&family=Montserrat:wght@400;700&family=Cabin:wght@400&display=swap">
<style>
  :root {
    --backdrop: #3a3a3c;
    --card: #f7f7f7;
    --ink: #1e1e1e;
    --ink-soft: #2c2c2c;
    --accent: #55b8e8;
    --rule: #4a4a4a;
  }
  * { margin: 0; padding: 0; box-sizing: border-box; }
  html, body { width: 1200px; height: 749px; overflow: hidden; }
  body { background: var(--backdrop); position: relative; }

  .card {
    position: absolute;
    left: 410px; top: 45px;
    width: 380px; height: 660px;
    background: var(--card);
    color: var(--ink);
    font-family: "Cabin", sans-serif;
  }
  .card__bar {
    position: absolute; left: 22%; width: 56%; height: 5px;
    background: var(--accent);
  }
  .card__bar--top { top: 0; }
  .card__bar--bottom { bottom: 0; }

  .brand {
    position: absolute; top: 112px; left: 0; width: 100%;
    text-align: center;
  }
  .brand__name {
    display: inline-flex; align-items: center; gap: 10px;
    font-family: "Josefin Sans", sans-serif;
    font-size: 34px; letter-spacing: 4px; color: var(--ink);
  }
  .brand__dot {
    width: 18px; height: 18px; border-radius: 50%;
    background: var(--ink);
  }
  .brand__tagline {
    margin-top: 8px;
    font-family: "Cabin Condensed", sans-serif;
    font-size: 16.5px; font-weight: 500; letter-spacing: -0.2px;
    color: var(--ink-soft);
  }

  .person {
    position: absolute; top: 245px; left: 125px;
    font-family: "Montserrat", sans-serif;
  }
  .person__name { font-size: 21px; font-weight: 700; line-height: 1.05; }
  .person__surname { color: var(--accent); }
  .person__title { font-size: 19px; font-weight: 400; line-height: 1.1; }

  .rule {
    position: absolute; left: 92px; width: 240px; height: 1px;
    background: var(--rule);
  }
  .rule--top { top: 338px; }
  .rule--bottom { top: 566px; }

  .contact {
    position: absolute; left: 112px; list-style: none;
    font-size: 15.5px; color: var(--ink-soft);
  }
  .contact--address { top: 356px; }
  .contact--lines { top: 424px; }
  .contact__item { display: flex; align-items: center; gap: 10px; height: 24px; }
  .contact--address .contact__item { height: auto; align-items: flex-start; }
  .contact__icon { width: 18px; height: 18px; flex: none; fill: var(--ink-soft); }
  .contact__icon--pin { width: 20px; height: 30px; margin-top: 4px; }
  .contact__address { line-height: 1.3; font-size: 15.5px; }
</style>
</head>
<body>
  <main class="card">
    <div class="card__bar card__bar--top"></div>

    <header class="brand">
      <div class="brand__name"><span class="brand__dot"></span>TALLIVO</div>
      <p class="brand__tagline">SCHEDULING &amp; ALLOCATION FOR FIELD CREWS</p>
    </header>

    <section class="person">
      <p class="person__name">Alex <span class="person__surname">Marlow</span></p>
      <p class="person__title">Job title here</p>
    </section>

    <div class="rule rule--top"></div>

    <ul class="contact contact--address">
      <li class="contact__item">
        <svg class="contact__icon contact__icon--pin" viewBox="0 0 20 30" aria-hidden="true">
          <path d="M10 0C4.5 0 0 4.4 0 9.8 0 17 10 30 10 30s10-13 10-20.2C20 4.4 15.5 0 10 0zm0 14a4.2 4.2 0 1 1 0-8.4 4.2 4.2 0 0 1 0 8.4z"/>
        </svg>
        <span class="contact__address">PO Box 512<br>Riverton NSW 2108</span>
      </li>
    </ul>

    <ul class="contact contact--lines">
      <li class="contact__item">
        <svg class="contact__icon" viewBox="0 0 20 20" aria-hidden="true">
          <path d="M2 7c0-2 3-4 8-4s8 2 8 4v2h-4V7.5c-1-.6-2.4-.8-4-.8s-3 .2-4 .8V9H2z"/>
          <path d="M4 11h12l2 6H2z"/>
        </svg>
        <span>502 418 6307</span>
      </li>
      <li class="contact__item">
        <svg class="contact__icon" viewBox="0 0 20 20" aria-hidden="true">
          <path d="M6 2h8v5H6z" fill="none" stroke="#2c2c2c" stroke-width="1.6"/>
          <path d="M2 8h16v10H2zM5 11v2h2v-2zm4 0v2h2v-2zm4 0v2h2v-2z"/>
        </svg>
        <span>502 418 6319</span>
      </li>
      <li class="contact__item">
        <svg class="contact__icon" viewBox="0 0 20 20" aria-hidden="true">
          <rect x="5" y="1" width="10" height="18" rx="1.5" fill="none" stroke="#2c2c2c" stroke-width="1.6"/>
          <circle cx="10" cy="16" r="1"/>
        </svg>
        <span>502 7734 2056</span>
      </li>
      <li class="contact__item">
        <svg class="contact__icon" viewBox="0 0 20 20" aria-hidden="true">
          <rect x="1.5" y="4" width="17" height="12" fill="none" stroke="#2c2c2c" stroke-width="1.5"/>
          <path d="M1.5 4l8.5 7 8.5-7" fill="none" stroke="#2c2c2c" stroke-width="1.5"/>
        </svg>
        <span>hello@tallivo.com.au</span>
      </li>
      <li class="contact__item">
        <svg class="contact__icon" viewBox="0 0 20 20" aria-hidden="true">
          <rect x="3.5" y="4" width="13" height="9" fill="none" stroke="#2c2c2c" stroke-width="1.5"/>
          <path d="M1 15h18v2H1z"/>
        </svg>
        <span>www.tallivo.com.au</span>
      </li>
    </ul>

    <div class="rule rule--bottom"></div>

    <div class="card__bar card__bar--bottom"></div>
  </main>
</body>
</html>
```